Super elegant, crisp & clean Business card design required

We recently upgraded our branding - which is on our website - talvendoraphoto.com

I would like a simple, yet elegant, clean business card design please.

The font of my logo is Cinzel - and because of the natural colour - it's best to have this on a black background.

I would like to have the back of the business card - with simply my logo.

PLEASE DO NOT SUBMIT A COMPLICATED / UNCLEAN DESIGN

Industry/Entity Type

Business

Contact Information for Business Card

Talven Doroshko Photography

Font styles to use
Other font styles liked:
• Cinzel

Requirements
Must have
• A backpage with nothing but my logo
• Simple design - stands out
Should not have
• Colour that dont align with my logo
• Over complicated '/ non symmetrical design

```html
<!DOCTYPE html>
<html lang="en">
<head>
<meta charset="utf-8">
<title>Talven Doroshko Photography – Business Card</title>
<link href="https://fonts.googleapis.com/css2?family=Cinzel:wght@400;700&display=swap" rel="stylesheet">
<style>
  :root {
    --backdrop: #5a5041;
    --card: #221e1b;
    --card-band: #2a2522;
    --gold: #a08e70;
    --gold-soft: #8d7c61;
  }
  * { margin: 0; padding: 0; box-sizing: border-box; }
  html, body { width: 1200px; height: 720px; overflow: hidden; }
  body {
    background: var(--backdrop);
    font-family: "Cinzel", serif;
    color: var(--gold);
    position: relative;
  }
  .card {
    position: absolute;
    width: 535px;
    height: 321px;
    background: var(--card);
    overflow: hidden;
  }
  .card--back { left: 582px; top: 291px; z-index: 1; }
  .card--front { left: 95px; top: 80px; z-index: 2; }

  .accent-bar {
    position: absolute;
    left: 262px;
    width: 10px;
    background: var(--gold);
  }
  .card--front .accent-bar--top { top: 0; height: 22px; }
  .card--back .accent-bar--top { top: 0; height: 62px; }
  .card--back .accent-bar--bottom { bottom: 0; height: 68px; }

  .brand {
    position: absolute;
    left: 0;
    width: 100%;
    text-align: center;
  }
  .brand__mark {
    display: block;
    margin: 0 auto 20px;
  }
  .brand__name {
    font-size: 20px;
    letter-spacing: 0.02em;
    line-height: 1;
    font-weight: 400;
  }
  .brand__tag {
    font-size: 10px;
    letter-spacing: 0.45em;
    line-height: 1;
    margin-top: 6px;
    padding-left: 0.45em;
    font-weight: 400;
  }
  .card--front .brand { top: 40px; }
  .card--back .brand { top: 95px; }

  .info-band {
    position: absolute;
    left: 0;
    top: 210px;
    width: 100%;
    height: 79px;
  }
  .info-band__person {
    position: absolute;
    left: 272px;
    top: 0;
    right: 0;
    height: 100%;
    background: var(--card-band);
  }
  .info-band .accent-bar { top: 0; height: 100%; }

  .contact {
    position: absolute;
    left: 29px;
    top: 16px;
    list-style: none;
    font-size: 11.5px;
    line-height: 18.5px;
    letter-spacing: 0.03em;
  }
  .person {
    position: absolute;
    right: 28px;
    top: 18px;
    text-align: right;
  }
  .person__name {
    font-size: 21px;
    line-height: 1;
    font-weight: 400;
    text-transform: uppercase;
  }
  .person__name strong { font-weight: 700; }
  .person__role {
    font-size: 13px;
    margin-top: 5px;
    color: var(--gold-soft);
  }
</style>
</head>
<body>
  <section class="card card--back" aria-label="Business card back">
    <span class="accent-bar accent-bar--top"></span>
    <div class="brand">
      <svg class="brand__mark" width="70" height="70" viewBox="0 0 70 70" aria-hidden="true">
        <circle cx="35" cy="35" r="33" fill="none" stroke="#a08e70" stroke-width="2"/>
      </svg>
      <p class="brand__name">Talven Doroshko</p>
      <p class="brand__tag">Photography</p>
    </div>
    <span class="accent-bar accent-bar--bottom"></span>
  </section>

  <section class="card card--front" aria-label="Business card front">
    <span class="accent-bar accent-bar--top"></span>
    <div class="brand">
      <svg class="brand__mark" width="70" height="70" viewBox="0 0 70 70" aria-hidden="true">
        <circle cx="35" cy="35" r="33" fill="none" stroke="#a08e70" stroke-width="2"/>
      </svg>
      <p class="brand__name">Talven Doroshko</p>
      <p class="brand__tag">Photography</p>
    </div>
    <div class="info-band">
      <div class="info-band__person"></div>
      <span class="accent-bar"></span>
      <ul class="contact">
        <li>07912580364</li>
        <li>www.talvendoraphoto.com</li>
        <li>mail@talvendoraphoto.com</li>
      </ul>
      <div class="person">
        <p class="person__name"><strong>Name</strong> Surname</p>
        <p class="person__role">Photographer</p>
      </div>
    </div>
  </section>
</body>
</html>
```